Copper Ridge Inquiries Letterhead

I would like to design a letterhead for a private investigation company. Our primary clients will be law firms. The business card is included below

```html
<!DOCTYPE html>
<html lang="en">
<head>
<meta charset="utf-8">
<title>Copper Ridge Inquiries Letterhead</title>
<link rel="stylesheet" href="https://fonts.googleapis.com/css2?family=Montserrat:wght@400;500;600;700&family=Open+Sans:wght@600&display=swap">
<style>
  :root {
    --navy: #1c3163;
    --orange: #ee5a2f;
    --body-grey: #6b6b6b;
    --rule: #c9c9c9;
    --backdrop: #ebebee;
    --paper: #ffffff;
    --signature-tone: #e9e9ec;
  }
  * { box-sizing: border-box; margin: 0; padding: 0; }
  html, body {
    width: 999px; height: 1200px; overflow: hidden;
    background: var(--backdrop);
    font-family: "Montserrat", sans-serif;
  }
  .letterhead {
    position: absolute; left: 100px; top: 40px;
    width: 798px; height: 1120px;
    background: var(--paper);
    overflow: hidden;
  }
  .brand {
    position: absolute; left: 55px; top: 110px;
    display: flex; align-items: center; gap: 8px;
    color: var(--navy); font-weight: 700; font-size: 17px; letter-spacing: 0.2px;
  }
  .brand-dot { width: 12px; height: 12px; border-radius: 50%; background: var(--orange); flex: none; }
  .contact-list {
    position: absolute; right: 75px; top: 74px;
    list-style: none; text-align: right;
  }
  .contact-list li {
    display: flex; justify-content: flex-end; align-items: center; gap: 5px;
    height: 24.3px;
    font-size: 10.5px; font-weight: 600; color: var(--navy); letter-spacing: 0.1px;
  }
  .contact-icon { width: 14px; height: 14px; flex: none; }
  .divider {
    position: absolute; left: 57px; top: 217px; width: 682px; height: 1px;
    background: var(--rule);
  }
  .recipient { position: absolute; left: 55px; top: 258px; color: var(--body-grey); font-size: 14px; }
  .recipient-name { color: var(--orange); font-size: 25px; font-weight: 600; line-height: 30px; margin-bottom: 14px; }
  .recipient p { line-height: 21px; margin-bottom: 15px; }
  .recipient p.address { margin-bottom: 0; }
  .date {
    position: absolute; right: 55px; top: 425px;
    font-family: "Open Sans", sans-serif; font-weight: 600; font-size: 18px; color: #555;
  }
  .letter-body {
    position: absolute; left: 57px; top: 471px; width: 686px;
    color: var(--body-grey); font-size: 15.5px; line-height: 24.7px;
    text-align: justify;
  }
  .letter-body p + p { margin-top: 24.6px; }
  .signature {
    position: absolute; left: 93px; top: 832px; width: 115px; height: 74px;
    background: linear-gradient(90deg, var(--signature-tone), #f6f6f7);
    border-radius: 4px;
  }
  .signer { position: absolute; left: 57px; top: 916px; color: var(--navy); font-size: 24px; font-weight: 700; }
  .footer-band { position: absolute; left: 0; bottom: 0; width: 506px; height: 12px; }
</style>
</head>
<body>
  <main class="letterhead">
    <div class="brand"><span class="brand-dot"></span>COPPER RIDGE INQUIRIES</div>

    <ul class="contact-list">
      <li>505.555.0142
        <svg class="contact-icon" viewBox="0 0 14 14"><circle cx="7" cy="7" r="7" fill="var(--orange)"/><path d="M4.3 3.6c.4-.3.9-.3 1.1.1l.6 1.1c.2.3.1.7-.2.9l-.4.3c.3.9 1 1.6 1.9 2l.3-.4c.2-.3.6-.4.9-.2l1.1.6c.4.2.4.7.1 1.1-.5.6-1.200.8-1.9.6-2-.6-3.5-2.1-4.1-4.1-.2-.7 0-1.5.6-2z" fill="#fff"/></svg>
      </li>
      <li>RIVERTON, NM
        <svg class="contact-icon" viewBox="0 0 14 14"><circle cx="7" cy="7" r="7" fill="var(--orange)"/><path d="M7 3c-1.6 0-2.7 1.2-2.7 2.7C4.3 7.7 7 11 7 11s2.7-3.3 2.7-5.3C9.7 4.2 8.6 3 7 3z" fill="#fff"/><circle cx="7" cy="5.8" r="1" fill="var(--orange)"/></svg>
      </li>
      <li>LICENSE NO. 04721356
        <svg class="contact-icon" viewBox="0 0 14 14"><circle cx="7" cy="7" r="7" fill="var(--orange)"/><circle cx="7" cy="5.3" r="1.8" fill="#fff"/><path d="M3.8 10.5c.4-1.7 1.7-2.6 3.2-2.6s2.8.9 3.2 2.6z" fill="#fff"/></svg>
      </li>
      <li>ELLIS@COPPERRIDGEINQUIRIES.COM
        <svg class="contact-icon" viewBox="0 0 14 14"><circle cx="7" cy="7" r="7" fill="var(--orange)"/><text x="7" y="10" text-anchor="middle" font-family="Montserrat, sans-serif" font-size="9" font-weight="700" fill="#fff">@</text></svg>
      </li>
    </ul>

    <div class="divider"></div>

    <section class="recipient">
      <h1 class="recipient-name">JONE SMITH</h1>
      <p>0123-456-789</p>
      <p>info@youremailaddress.com</p>
      <p class="address">1234 City Your Ln. Suite<br>123 Dallas, TX 0000</p>
    </section>

    <div class="date">12 December, 2024</div>

    <section class="letter-body">
      <p>Lorem ipsum dolor sit amet, consectetuer adipiscing elit, sed diam nonummy nibh euis&shy;mod tincidunt ut laoreet dolore magna aliquam erat volutpat. Ut wisi enim ad minim veniam, quis nostrud exerci tation ullamcorper suscipit lobortis nisl ut aliquip ex ea com&shy;modo consequat. Duis autem vel eum iriure dolor in hendrerit in vulputate velit esse mo&shy;lestie consequat, vel illum dolore eu feugiat nulla facilisis at vero eros et accumsan et iusto odio dignissim qui blandit praesent luptatum zzril delenit augue duis dolore te feu&shy;gait nulla facilisi.</p>
      <p>Lorem ipsum dolor sit amet, cons ectetuer adipiscing elit, sed diam nonummy nibh euis&shy;mod tincidunt ut laoreet dolore magna aliquam erat volutpat. Ut wisi enim ad minim veniam, quis nostrud exerci tation ullamcorper suscipit lobortis nisl ut aliquip ex ea com&shy;modo consequat.</p>
    </section>

    <div class="signature" role="img" aria-label="Handwritten signature of the sender"></div>
    <div class="signer">Mr. Jone Smith</div>

    <svg class="footer-band" viewBox="0 0 506 12" preserveAspectRatio="none"><polygon points="0,0 506,0 500,12 0,12" fill="var(--navy)"/></svg>
  </main>
</body>
</html>
```